Salon and Spa Distributor Business Card

Need a business card. We are are distributor in the salon and spa industry. We identify with natural beauty. Need a card with:
Company Name: Petal Quarry"
Title: "President & CEO"
Address
Company Phone number
email
website
Tag Line:" The Professional Salon Source"

Industry/Entity Type

Business

Contact Information for Business Card

Name: Dov Strommen
Title: "President & CEO"
Address: 31 Harlow Ln, Bexmoor, NJ 07813
Company Phone number: 800-463-5918
email: dovstrommen@petalquarry.example
website: www.petalquarry.example

Requirements
Should not have
• No black backgrounds

```html
<!DOCTYPE html>
<html lang="en">
<head>
<meta charset="utf-8">
<title>Petal Quarry Business Card</title>
<link rel="stylesheet" href="https://fonts.googleapis.com/css2?family=Questrial&display=swap">
<style>
  :root {
    --bg: #e9ece8;
    --green-light: #6cc04a;
    --green-mid: #3fa33e;
    --green-dark: #0f7434;
    --white: #ffffff;
    --ink: #1b1b1b;
    --swoosh: #111111;
  }
  html, body {
    margin: 0;
    padding: 0;
    width: 1200px;
    height: 880px;
    overflow: hidden;
    background: var(--bg);
    font-family: "Questrial", "Century Gothic", sans-serif;
  }
  .canvas {
    position: relative;
    width: 1200px;
    height: 880px;
  }
  .card {
    position: absolute;
    left: 270px;
    width: 660px;
    height: 377px;
    border-radius: 22px;
    overflow: hidden;
    box-shadow: 0 10px 28px rgba(0,0,0,0.18);
  }
  .card-front {
    top: 40px;
    background: linear-gradient(160deg, var(--green-light) 0%, var(--green-mid) 45%, var(--green-dark) 100%);
  }
  .card-back {
    top: 463px;
    background: var(--white);
  }

  /* Front */
  .front-art {
    position: absolute;
    left: 30px;
    top: 30px;
    width: 320px;
    height: 317px;
    border-radius: 50%;
    background: radial-gradient(circle, rgba(30,130,60,0.35) 0%, rgba(30,130,60,0) 70%);
  }
  .front-brand {
    position: absolute;
    right: 44px;
    bottom: 92px;
    text-align: right;
    color: var(--white);
  }
  .front-brand .brand-name {
    font-size: 50px;
    letter-spacing: 0.5px;
    line-height: 1;
  }
  .front-brand .tagline {
    font-size: 17px;
    letter-spacing: 1px;
    margin-top: 8px;
  }

  /* Back */
  .back-band {
    position: absolute;
    inset: 0;
  }
  .person {
    position: absolute;
    right: 40px;
    top: 30px;
    text-align: right;
    color: var(--white);
  }
  .person .name { font-size: 24px; }
  .person .title { font-size: 15px; margin-top: 3px; }

  .back-brand {
    position: absolute;
    left: 110px;
    top: 182px;
    display: flex;
    align-items: center;
    gap: 14px;
    color: var(--green-mid);
  }
  .back-brand .mark-dot {
    width: 22px;
    height: 22px;
    border-radius: 50%;
    background: var(--green-mid);
  }
  .back-brand .brand-name {
    font-size: 40px;
    line-height: 1;
  }

  .contacts {
    position: absolute;
    left: 40px;
    bottom: 28px;
    color: var(--ink);
    font-size: 16px;
  }
  .contact-row {
    display: flex;
    align-items: center;
    gap: 10px;
    margin-top: 6px;
  }
  .contact-icon {
    width: 18px;
    height: 18px;
    border-radius: 3px;
    background: var(--green-mid);
    display: flex;
    align-items: center;
    justify-content: center;
  }
  .address {
    position: absolute;
    right: 40px;
    bottom: 70px;
    text-align: right;
    color: var(--ink);
    font-size: 16px;
    line-height: 1.4;
  }
</style>
</head>
<body>
<main class="canvas">

  <section class="card card-front">
    <div class="front-art" role="img" aria-label="Soft green leaf and flowing hair illustration area"></div>
    <div class="front-brand">
      <div class="brand-name">Petal Quarry</div>
      <div class="tagline">The Professional Salon Source</div>
    </div>
  </section>

  <section class="card card-back">
    <svg class="back-band" width="660" height="377" viewBox="0 0 660 377" aria-hidden="true">
      <defs>
        <linearGradient id="bandGrad" x1="0" y1="0" x2="1" y2="1">
          <stop offset="0" stop-color="#5cb845"/>
          <stop offset="1" stop-color="#1f8a3a"/>
        </linearGradient>
      </defs>
      <path d="M0 0 H660 V128 C470 70 220 70 0 150 Z" fill="url(#bandGrad)"/>
      <path d="M30 152 C230 80 470 78 660 132 L660 140 C470 92 240 92 30 152 Z" fill="#111111"/>
    </svg>

    <div class="person">
      <div class="name">Dov Strommen</div>
      <div class="title">President &amp; CEO</div>
    </div>

    <div class="back-brand">
      <span class="mark-dot"></span>
      <span class="brand-name">Petal Quarry</span>
    </div>

    <div class="address">31 Harlow Ln,<br>Bexmoor, NJ 07813</div>

    <div class="contacts">
      <div class="contact-row">
        <span class="contact-icon">
          <svg width="12" height="12" viewBox="0 0 24 24" aria-hidden="true"><path fill="#fff" d="M6.6 10.8a15 15 0 0 0 6.6 6.6l2.2-2.2c.3-.3.7-.4 1-.2 1.1.4 2.3.6 3.6.6.6 0 1 .4 1 1V20c0 .6-.4 1-1 1A17 17 0 0 1 3 4c0-.6.4-1 1-1h3.5c.6 0 1 .4 1 1 0 1.3.2 2.5.6 3.6.1.3 0 .7-.2 1z"/></svg>
        </span>800-463-5918
      </div>
      <div class="contact-row">
        <span class="contact-icon">
          <svg width="12" height="12" viewBox="0 0 24 24" aria-hidden="true"><path fill="none" stroke="#fff" stroke-width="2.4" d="M3 6h18v12H3z M3 6l9 7 9-7"/></svg>
        </span>dovstrommen@petalquarry.example
      </div>
      <div class="contact-row">
        <span class="contact-icon">
          <svg width="12" height="12" viewBox="0 0 24 24" aria-hidden="true"><g fill="none" stroke="#fff" stroke-width="2"><circle cx="12" cy="12" r="9"/><path d="M3 12h18M12 3c3 3 3 15 0 18M12 3c-3 3-3 15 0 18"/></g></svg>
        </span>www.petalquarry.example
      </div>
    </div>
  </section>

</main>
</body>
</html>
```